KPV Datacore Solutions

We need a Logo and Website for our company based in London. We are a IT recruitment company . We provide quality resources to top IT company across UK.

Industry/Entity Type

It Company

Number of Pages Required

4 page

```html
<!DOCTYPE html>
<html lang="en">
<head>
<meta charset="utf-8">
<title>KPV Datacore Solutions – Recruitment Company</title>
<link rel="stylesheet" href="https://fonts.googleapis.com/css2?family=Ubuntu:wght@400;500;700&family=Open+Sans:ital,wght@0,400;0,600;1,400;1,600&display=swap">
<style>
:root{
  --blue:#1ba8dc;
  --blue-dark:#1590c0;
  --yellow:#e8b90f;
  --ink:#333333;
  --text:#666666;
  --muted:#888888;
  --line:#e4e4e4;
  --panel:#f4f3ee;
  --footer:#1c1c1c;
  --white:#ffffff;
}
*{box-sizing:border-box;margin:0;padding:0}
html,body{width:1200px;height:3056px;overflow:hidden}
body{position:relative;background:var(--white);font-family:"Open Sans",Arial,sans-serif;color:var(--text)}
.abs{position:absolute}
h1,h2,h3,h4{font-family:"Ubuntu",Arial,sans-serif;font-weight:400;color:var(--ink)}

/* top bar */
.topbar{left:0;top:0;width:1200px;height:30px;background:var(--blue);color:var(--white);font-size:12px;display:flex;align-items:center;justify-content:flex-end;padding-right:55px;gap:8px}
.topbar strong{font-weight:600;letter-spacing:.5px}

/* header */
.header{left:0;top:30px;width:1200px;height:98px;background:var(--white)}
.brand{left:98px;top:26px;display:flex;align-items:center;gap:10px}
.brand-mark{width:46px;height:46px;border:2px solid var(--ink);display:flex;align-items:center;justify-content:center;font-family:"Ubuntu",sans-serif;font-size:14px;color:var(--ink)}
.brand-name{font-family:"Ubuntu",sans-serif;font-size:22px;color:var(--ink);line-height:1}
.brand-name small{display:block;font-size:14px;color:var(--ink);margin-top:2px}
.nav{right:98px;top:36px;display:flex;gap:0}
.nav a{font-family:"Ubuntu",sans-serif;font-size:12px;color:var(--ink);text-decoration:none;padding:7px 14px;margin-left:16px}
.nav a.active{border:1px solid var(--blue);color:var(--blue)}

/* hero */
.hero{left:0;top:128px;width:1200px;height:489px;background:linear-gradient(100deg,#6b7a84 0%,#8d9aa2 30%,#a8b4ba 55%,#5d6e7a 80%,#3e4f5c 100%)}
.hero-text{left:115px;top:185px;width:440px}
.hero-text h1{color:var(--white);font-family:"Ubuntu",sans-serif;font-weight:700;font-size:44px;line-height:1.05;letter-spacing:.5px}
.hero-text p{color:var(--white);font-size:14px;line-height:1.45;margin-top:10px}
.hero-arrow{top:360px;width:20px;height:30px}

/* welcome */
.welcome{left:0;top:660px;width:1200px;text-align:center}
.welcome h2{font-size:32px}
.welcome p{width:880px;margin:18px auto 0;font-size:11.5px;line-height:23px;color:var(--text)}
.features{left:98px;top:819px;width:1004px;height:255px;background:var(--panel);border:1px solid #ebe9e2;display:flex}
.feature{flex:1;text-align:center;padding-top:30px;border-right:1px solid #e8e6de}
.feature:last-child{border-right:0}
.feature-icon{width:92px;height:92px;border-radius:50%;background:var(--blue);margin:0 auto;display:flex;align-items:center;justify-content:center}
.feature h3{font-size:14px;margin-top:42px;color:var(--ink)}
.feature p{font-size:11.5px;line-height:20px;margin:10px auto 0;width:290px}

/* jobs */
.section-title{font-family:"Ubuntu",sans-serif;font-size:26px;color:var(--ink)}
.section-title span{color:var(--blue)}
.recent-title{left:98px;top:1112px}
.job-list{left:98px;top:1171px;width:666px;border-top:2px solid var(--blue)}
.job{height:112px;border:1px solid var(--line);border-top:0;position:relative}
.job-thumb{position:absolute;left:18px;top:28px;width:62px;height:56px}
.job h4{position:absolute;left:98px;top:22px;font-size:15.5px;color:var(--ink)}
.job-meta{position:absolute;left:98px;top:54px;display:flex;gap:22px;font-size:11px;color:var(--muted)}
.job-meta span{display:flex;align-items:center;gap:6px}
.btn-yellow{position:absolute;right:18px;top:40px;width:92px;height:34px;background:var(--yellow);color:var(--ink);font-size:12px;display:flex;align-items:center;justify-content:center;border-radius:2px}

.spot-title{left:798px;top:1112px}
.spotlight{left:798px;top:1171px;width:304px;height:271px;border:1px solid var(--line);border-top:2px solid var(--blue);padding:20px 20px}
.spotlight h4{font-size:15px;line-height:22px;color:var(--ink)}
.spotlight .job-meta{position:static;margin-top:12px}
.spotlight p{font-size:11.5px;line-height:20px;margin-top:14px}
.btn-blue{display:inline-block;margin-top:16px;background:var(--blue);color:var(--white);font-size:12px;padding:9px 20px;border-radius:2px}
.subscribe{left:798px;top:1467px;width:304px;height:159px;background:var(--yellow);padding:28px 24px}
.subscribe-head{display:flex;gap:14px;align-items:flex-start}
.subscribe-head h4{font-size:14px;line-height:22px;color:var(--ink);letter-spacing:.5px}
.subscribe-form{display:flex;margin-top:10px}
.subscribe-form .field{width:172px;height:32px;background:var(--white);font-size:11px;color:var(--text);padding:9px 12px}
.subscribe-form .go{width:82px;height:32px;background:#333;color:var(--white);font-size:11px;display:flex;align-items:center;justify-content:center}

/* testimonial */
.testimonial{left:0;top:1672px;width:1200px;height:467px;background:linear-gradient(90deg,#1b97d0,#1fa6e0 50%,#1a8fc7);text-align:center;color:var(--white)}
.avatar{left:550px;top:65px;width:100px;height:100px;transform:rotate(45deg);background:var(--white);padding:6px}
.avatar div{width:100%;height:100%;background:linear-gradient(135deg,#c9c3bd,#5b5f6a)}
.quote{left:170px;top:245px;width:860px;font-style:italic;font-size:13px;line-height:25px}
.quote-by{left:0;top:342px;width:1200px;font-style:italic;font-size:15px}
.quote-by strong{font-weight:600}
.dots{left:493px;top:388px;display:flex;gap:9px}
.dots i{display:block;width:42px;height:5px;background:rgba(255,255,255,.45)}
.dots i.on{background:var(--yellow)}

/* candidates */
.cand-head{left:0;top:2200px;width:1200px;text-align:center}
.cand-head h2{font-size:30px;font-weight:500;letter-spacing:.5px}
.cand-head p{font-size:13px;color:var(--text);margin-top:2px}
.cand-head hr{width:38px;border:0;border-top:3px solid var(--blue);margin:8px auto 0}
.card{top:2304px;width:244px;height:334px;text-align:center}
.card.featured{border:2px solid #55bfe6;padding:10px}
.card-photo{width:244px;height:231px}
.card.featured .card-info{height:219px;background:#5ec3ea;color:var(--white);padding:18px 16px}
.card-info h5{font-family:"Ubuntu",sans-serif;font-size:15px;font-weight:500}
.card-info p{font-size:11px;line-height:20px;margin-top:10px}
.card-name{font-family:"Ubuntu",sans-serif;font-size:19px;color:var(--ink);margin-top:14px}
.card-role{font-size:10.5px;color:var(--ink);margin-top:4px}
.card-social{display:flex;gap:5px;justify-content:center;margin-top:10px}
.card-social i{display:block;width:22px;height:22px;border:1px solid #999;border-radius:50%}

/* footer */
.footer{left:0;top:2709px;width:1200px;height:285px;background:linear-gradient(180deg,#161616,#262626);color:#ddd}
.footer h4{font-family:"Ubuntu",sans-serif;font-size:15px;font-weight:500;color:var(--white);letter-spacing:.3px}
.footer h4 span{color:var(--blue)}
.f-contact{left:98px;top:48px;width:260px;font-size:12.5px;line-height:20px}
.f-contact p{margin-top:12px}
.f-row{display:flex;gap:14px;align-items:flex-start;margin-top:10px}
.f-links{left:413px;top:48px}
.f-links ul{list-style:none;margin-top:12px}
.f-links li{font-size:11.5px;line-height:29px;display:flex;align-items:center;gap:10px}
.f-links li::before{content:"";border-left:6px solid #ddd;border-top:4px solid transparent;border-bottom:4px solid transparent}
.f-location{left:623px;top:48px}
.map{margin-top:12px;width:277px;height:138px;background:linear-gradient(135deg,#c9dbe6,#e9ecef 50%,#bcd3e2);border:3px solid var(--white)}
.f-brand{left:980px;top:30px;width:88px;text-align:center}
.f-mark{width:88px;height:82px;border:3px solid var(--white);display:flex;align-items:center;justify-content:center;font-family:"Ubuntu",sans-serif;font-size:26px;color:var(--white)}
.f-social{display:flex;gap:5px;justify-content:center;margin-top:10px}
.f-social i{display:block;width:22px;height:22px;border:1px solid #aaa;border-radius:50%}
.copyright{left:0;top:2994px;width:1200px;height:62px;background:var(--blue);color:var(--white);font-size:11.5px;display:flex;align-items:center;justify-content:center}
</style>
</head>
<body>

<div class="abs topbar">
  <svg width="12" height="14" viewBox="0 0 12 14"><path d="M6 0a5 5 0 0 0-5 5c0 4 5 9 5 9s5-5 5-9a5 5 0 0 0-5-5zm0 7a2 2 0 1 1 0-4 2 2 0 0 1 0 4z" fill="#fff"/></svg>
  <strong>QUICK CONTACT :</strong> 12 Harbour Lane London E9 7QT
</div>

<header class="abs header">
  <div class="abs brand">
    <div class="brand-mark">KPV</div>
    <div class="brand-name">Datacore<small>Solutions</small></div>
  </div>
  <nav class="abs nav">
    <a class="active">HOME</a><a>FOR CANDIDATES</a><a>FOR EMPLOYERS</a><a>BLOG</a><a>CONTACT US</a>
  </nav>
</header>

<section class="abs hero" role="img" aria-label="Photo of colleagues working together at a laptop in a bright office">
  <div class="abs hero-text">
    <h1>RECRUITMENT<br>COMPANY</h1>
    <p>Lorem ipsum dolor sit amet, consectetur adipiscing sed do eiusmod tempor incididunt ut labore et</p>
  </div>
  <svg class="abs hero-arrow" style="left:50px" viewBox="0 0 20 30"><path d="M14 6 6 15l8 9" stroke="#fff" stroke-width="2.5" fill="none"/></svg>
  <svg class="abs hero-arrow" style="right:50px" viewBox="0 0 20 30"><path d="m6 6 8 9-8 9" stroke="#fff" stroke-width="2.5" fill="none"/></svg>
</section>

<section class="abs welcome">
  <h2>Welcome To KPV Datacore Solutions</h2>
  <p>Lorem Ipsum is simply dummy text of the printing and typesetting industry. Lorem Ipsum has been the industry's standard dummy text ever since the 1500s, when an unknown printer took a galley of type and scrambled it to make a type specimen book. It has survived not only five centuries, but also the leap into electronic typesetting, remaining essentially unchanged. Lorem Ipsum is simply dummy text of the printing and typesetting industry.</p>
</section>

<section class="abs features">
  <div class="feature">
    <div class="feature-icon"><svg width="40" height="40" viewBox="0 0 40 40" fill="#fff"><circle cx="16" cy="12" r="7"/><path d="M3 34c0-8 6-13 13-13s13 5 13 13z"/><rect x="27" y="22" width="10" height="3"/><rect x="30.5" y="18.5" width="3" height="10"/></svg></div>
    <h3>REGISTER AN ACCOUNT</h3>
    <p>Lorem ipsum dolor sit amet, consectetur adipiscing elit, sed do eiusmod tempor incididunt</p>
  </div>
  <div class="feature">
    <div class="feature-icon"><svg width="38" height="38" viewBox="0 0 38 38"><circle cx="16" cy="16" r="10" stroke="#fff" stroke-width="4" fill="none"/><path d="m23 23 10 10" stroke="#fff" stroke-width="5" stroke-linecap="round"/></svg></div>
    <h3>SEARCH YOUR JOB</h3>
    <p>Lorem ipsum dolor sit amet, consectetur adipiscing elit, sed do eiusmod tempor incididunt</p>
  </div>
  <div class="feature">
    <div class="feature-icon"><svg width="32" height="38" viewBox="0 0 32 38"><path d="M2 2h19l9 9v25H2z" fill="#fff"/><path d="M21 2v9h9" fill="#d0eef9"/><path d="M8 18h16M8 24h16M8 30h12" stroke="#1ba8dc" stroke-width="2"/></svg></div>
    <h3>SEND YOUR RESUME</h3>
    <p>Lorem ipsum dolor sit amet, consectetur adipiscing elit, sed do eiusmod tempor incididunt</p>
  </div>
</section>

<h2 class="abs section-title recent-title">Recent <span>Jobs</span></h2>
<div class="abs job-list">
  <div class="job">
    <div class="job-thumb" role="img" aria-label="Thumbnail of a tree" style="background:linear-gradient(180deg,#a9d3ee,#9bc46a)"></div>
    <h4>Marketing Coordinator - SEO / SEM Experience FULL-TIME</h4>
    <div class="job-meta"><span><svg width="10" height="11" viewBox="0 0 10 11"><path d="M1 1h8v10H1z" fill="#999"/></svg>Company Name</span><span><svg width="8" height="11" viewBox="0 0 8 11"><path d="M4 0a4 4 0 0 0-4 4c0 3 4 7 4 7s4-4 4-7a4 4 0 0 0-4-4z" fill="#999"/></svg>12 Harbour Lane London</span><span><svg width="10" height="10" viewBox="0 0 10 10"><path d="M0 2h10v8H0z" fill="#999"/><path d="M1 4h8" stroke="#fff"/></svg>Jan 10, 2016</span></div>
    <div class="btn-yellow">View More</div>
  </div>
  <div class="job">
    <div class="job-thumb" role="img" aria-label="Thumbnail of a globe" style="background:radial-gradient(circle,#d8c27a,#6b8fb8)"></div>
    <h4>Marketing Coordinator - SEO / SEM Experience FULL-TIME</h4>
    <div class="job-meta"><span><svg width="10" height="11" viewBox="0 0 10 11"><path d="M1 1h8v10H1z" fill="#999"/></svg>Company Name</span><span><svg width="8" height="11" viewBox="0 0 8 11"><path d="M4 0a4 4 0 0 0-4 4c0 3 4 7 4 7s4-4 4-7a4 4 0 0 0-4-4z" fill="#999"/></svg>12 Harbour Lane London</span><span><svg width="10" height="10" viewBox="0 0 10 10"><path d="M0 2h10v8H0z" fill="#999"/><path d="M1 4h8" stroke="#fff"/></svg>Jan 10, 2016</span></div>
    <div class="btn-yellow">View More</div>
  </div>
  <div class="job">
    <div class="job-thumb" role="img" aria-label="Thumbnail of hands on a keyboard" style="background:linear-gradient(135deg,#8aa3c4,#3c5a86)"></div>
    <h4>Marketing Coordinator - SEO / SEM Experience FULL-TIME</h4>
    <div class="job-meta"><span><svg width="10" height="11" viewBox="0 0 10 11"><path d="M1 1h8v10H1z" fill="#999"/></svg>Company Name</span><span><svg width="8" height="11" viewBox="0 0 8 11"><path d="M4 0a4 4 0 0 0-4 4c0 3 4 7 4 7s4-4 4-7a4 4 0 0 0-4-4z" fill="#999"/></svg>12 Harbour Lane London</span><span><svg width="10" height="10" viewBox="0 0 10 10"><path d="M0 2h10v8H0z" fill="#999"/><path d="M1 4h8" stroke="#fff"/></svg>Jan 10, 2016</span></div>
    <div class="btn-yellow">View More</div>
  </div>
  <div class="job">
    <div class="job-thumb" role="img" aria-label="Thumbnail of a tablet" style="background:linear-gradient(135deg,#eeeeee,#9aa3aa)"></div>
    <h4>Marketing Coordinator - SEO / SEM Experience FULL-TIME</h4>
    <div class="job-meta"><span><svg width="10" height="11" viewBox="0 0 10 11"><path d="M1 1h8v10H1z" fill="#999"/></svg>Company Name</span><span><svg width="8" height="11" viewBox="0 0 8 11"><path d="M4 0a4 4 0 0 0-4 4c0 3 4 7 4 7s4-4 4-7a4 4 0 0 0-4-4z" fill="#999"/></svg>12 Harbour Lane London</span><span><svg width="10" height="10" viewBox="0 0 10 10"><path d="M0 2h10v8H0z" fill="#999"/><path d="M1 4h8" stroke="#fff"/></svg>Jan 10, 2016</span></div>
    <div class="btn-yellow">View More</div>
  </div>
</div>

<h2 class="abs section-title spot-title"><span>Job</span> Spotlight</h2>
<aside class="abs spotlight">
  <h4>Social Media :<br>Advertising Coordinator</h4>
  <div class="job-meta"><span><svg width="8" height="11" viewBox="0 0 8 11"><path d="M4 0a4 4 0 0 0-4 4c0 3 4 7 4 7s4-4 4-7a4 4 0 0 0-4-4z" fill="#999"/></svg>12 Harbour Lane London</span><span><svg width="10" height="10" viewBox="0 0 10 10"><path d="M0 2h10v8H0z" fill="#999"/><path d="M1 4h8" stroke="#fff"/></svg>Jan 10, 2016</span></div>
  <p>Lorem ipsum dolor sit amet, consectetur adipiscing elit, sed do eiusmod tempor incididunt ut labore et dolore magna aliqua. Ut enim ad minim veniam, quis nostrud exercitation</p>
  <span class="btn-blue">APPLY FOR THIS JOB</span>
</aside>
<aside class="abs subscribe">
  <div class="subscribe-head">
    <svg width="40" height="36" viewBox="0 0 40 36"><path d="M2 14 20 2l18 12v22H2z" fill="#fff"/><path d="M8 8h24v14H8z" fill="#f6e7b0"/><path d="M2 14l18 12 18-12" stroke="#e8b90f" stroke-width="2" fill="none"/></svg>
    <h4>SUBSCRIBE TO<br>FOLLOW</h4>
  </div>
  <div class="subscribe-form"><div class="field">Email Address</div><div class="go">SIGN UP</div></div>
</aside>

<section class="abs testimonial" role="img" aria-label="Blue tinted photo of a person working at a desk">
  <div class="abs avatar"><div role="img" aria-label="Portrait of the managing partner"></div></div>
  <p class="abs quote">“ Lorem ipsum dolor sit amet, consectetur adipiscing elit, sed do eiusmod tempor incididunt ut labore et dolore magna aliqua. Ut enim ad minim veniam, quis nostrud exercitation ullamco laboris nisi ut aliquip ex ea commodo consequat. Duis aute irure dolor in reprehenderit in voluptate velit esse cillum dolore eu fugiat nulla pariatur. Excepteur sint occaecat ”</p>
  <p class="abs quote-by"><strong>John Doe</strong> - Managing Partner</p>
  <div class="abs dots"><i class="on"></i><i></i><i></i></div>
</section>

<section class="abs cand-head">
  <h2>RECRUITMENT CANDIDATES</h2>
  <p>We are added our featured works below</p>
  <hr>
</section>

<div class="abs card featured" style="left:106px">
  <div class="card-info">
    <h5>CANDIDATES</h5>
    <p>Lorem ipsum dolor sit amet, consectetur adipiscing elit, sed do eiusmod tempor incididunt ut labore et dolore magna aliqua. Ut enim ad minim veniam, quis nostrud exercitation</p>
  </div>
  <div class="card-name" style="margin-top:8px">JOHN DOE</div>
  <div class="card-role">Senior Designer</div>
  <div class="card-social"><i></i><i></i><i></i><i></i></div>
</div>
<div class="abs card" style="left:355px">
  <div class="card-photo" role="img" aria-label="Photo of a candidate in a dark suit" style="background:linear-gradient(180deg,#eef0f2,#3a4150)"></div>
  <div class="card-name">JOHN DOE</div><div class="card-role">Senior Designer</div>
</div>
<div class="abs card" style="left:603px">
  <div class="card-photo" role="img" aria-label="Photo of a candidate in a beige jacket" style="background:linear-gradient(180deg,#9aa6b2,#cdb9a3)"></div>
  <div class="card-name">JOHN DOE</div><div class="card-role">Product Designer</div>
</div>
<div class="abs card" style="left:850px">
  <div class="card-photo" role="img" aria-label="Photo of a candidate at a laptop" style="background:linear-gradient(180deg,#e4e8ea,#8e9aa6)"></div>
  <div class="card-name">JOHN DOE</div><div class="card-role">Developer</div>
</div>

<footer class="abs footer">
  <div class="abs f-contact">
    <h4>CONTACT <span>US</span></h4>
    <p>KPV Datacore Solutions, 12 Harbour Lane London E9 7QT</p>
    <div class="f-row"><svg width="16" height="16" viewBox="0 0 16 16"><path d="M3 1l3 3-2 2c1 3 3 5 6 6l2-2 3 3-2 2C7 15 1 9 1 3z" stroke="#ddd" fill="none" stroke-width="1.3"/></svg><span>Call Us (020) 555 - 0142<br>(020) 555 - 0187</span></div>
    <div class="f-row"><svg width="18" height="13" viewBox="0 0 18 13"><path d="M1 1h16v11H1z M1 1l8 6 8-6" stroke="#ddd" fill="none" stroke-width="1.3"/></svg><span>info@kpvdatacore.example</span></div>
  </div>
  <div class="abs f-links">
    <h4>QUICK <span>LINKS</span></h4>
    <ul><li>HOME</li><li>ABOUT US</li><li>CANDIDATES</li><li>SEARCH FOR JOBS</li><li>POST A JOB</li></ul>
  </div>
  <div class="abs f-location">
    <h4>OUR <span>LOCATION</span></h4>
    <div class="map" role="img" aria-label="Street map of the office location"></div>
  </div>
  <div class="abs f-brand">
    <div class="f-mark">KPV</div>
    <div class="f-social"><i></i><i></i><i></i><i></i><i></i></div>
  </div>
</footer>
<div class="abs copyright">2016 © KPV Datacore Solutions.All Rights Reserved</div>

</body>
</html>
```